Local Flower Farm Needs Business Card Design

I need business cards designed for a flower farm based in Eudora, Kansas.
Business Info:
We are a local cut flower farm located in Eudora, Kansas, founded by Corinne Haldwick. What started as a passion for agriculture and search for more joy in daily life has blossomed into a small business dedicated to providing the community with beautiful, fresh, and sustainable flowers. We specialize in local, seasonal blooms, ensuring that every petal reflects the care and dedication we pour into our craft. Our mission is to deliver the highest quality flowers directly to our customers through local farmers markets and to florists who share our commitment to sustainability. Join us in celebrating the beauty of nature, one bloom at a time!
Contact Details:
Corinne Haldwick
Owner
Phone 913-555-0147
Facebook: Rosalind Thorpe Gardens
Instagram: @RosalindThorpeGardens
Website: RosalindThorpeGardens.example
Target Market(s)
Wholesale to Florists and Direct to Consumer via Farmers Market
Industry/Entity Type
Florist, Farm
Contact Information for Business Card
Name, Contact Info, Logo
Look and feel
Each slider illustrates characteristics of the customer's brand and the style your logo design should communicate.

```html
<!DOCTYPE html>
<html lang="en">
<head>
<meta charset="utf-8">
<title>Rosalind Thorpe Gardens – Business Card</title>
<link rel="stylesheet" href="https://fonts.googleapis.com/css2?family=Montserrat:wght@400;500;700&display=swap">
<style>
  :root {
    --backdrop: #6f5a45;
    --card-white: #ffffff;
    --ink: #0f2a2c;
    --ink-soft: #1c3335;
    --faint: #e3e3e3;
    --teal-deep: #0b2a30;
    --teal-raised: #16444b;
    --teal-line: #1f5059;
  }
  * { margin: 0; padding: 0; box-sizing: border-box; }
  html, body { width: 900px; height: 1200px; overflow: hidden; }
  body {
    background: var(--backdrop);
    font-family: "Montserrat", sans-serif;
    position: relative;
  }
  .card {
    position: absolute;
    width: 743px;
    height: 440px;
    border-radius: 24px;
    overflow: hidden;
  }
  .card--front { left: 80px; top: 131px; background: var(--card-white); }
  .card--back { left: 78px; top: 638px; background: var(--teal-deep); }

  .brand-seal {
    position: absolute;
    left: 34px; top: 37px;
    width: 158px; height: 158px;
    border: 1.5px solid var(--ink);
    border-radius: 50%;
    display: flex; align-items: center; justify-content: center;
    text-align: center;
  }
  .brand-seal__name {
    font-weight: 700;
    font-size: 15px;
    line-height: 1.3;
    color: var(--ink);
    letter-spacing: 0.5px;
  }

  .brand-watermark {
    position: absolute;
    right: 40px; top: 40px;
    width: 340px;
    text-align: center;
    font-weight: 700;
    font-size: 62px;
    line-height: 1.12;
    color: var(--faint);
  }

  .contact { position: absolute; left: 37px; top: 238px; color: var(--ink); }
  .contact__name { font-weight: 700; font-size: 25px; letter-spacing: 0.2px; color: var(--ink); }
  .contact__role { font-size: 15px; margin-top: 3px; color: var(--ink-soft); }
  .contact__list { list-style: none; margin-top: 18px; }
  .contact__item {
    display: flex; align-items: center; gap: 9px;
    font-size: 16px; height: 25.5px; color: var(--ink);
  }
  .contact__icon { width: 15px; height: 15px; flex: none; }

  .brand-emboss {
    position: absolute;
    left: 202px; top: 64px;
    width: 340px; height: 340px;
    border: 2px solid var(--teal-line);
    border-radius: 50%;
    display: flex; align-items: center; justify-content: center;
    text-align: center;
  }
  .brand-emboss__name {
    font-weight: 700;
    font-size: 34px;
    line-height: 1.25;
    color: var(--teal-raised);
    letter-spacing: 1px;
  }
</style>
</head>
<body>

<section class="card card--front" aria-label="Card front">
  <div class="brand-seal">
    <span class="brand-seal__name">Rosalind<br>Thorpe<br>Gardens</span>
  </div>

  <div class="brand-watermark" aria-hidden="true">Rosalind<br>Thorpe<br>Gardens</div>

  <div class="contact">
    <h1 class="contact__name">Corinne Haldwick</h1>
    <p class="contact__role">Owner</p>
    <ul class="contact__list">
      <li class="contact__item">
        <svg class="contact__icon" viewBox="0 0 24 24" aria-hidden="true"><path fill="var(--ink)" d="M6.6 10.8c1.4 2.8 3.8 5.1 6.6 6.6l2.2-2.2c.3-.3.7-.4 1-.2 1.1.4 2.3.6 3.6.6.6 0 1 .4 1 1V20c0 .6-.4 1-1 1C10.6 21 3 13.4 3 4c0-.6.4-1 1-1h3.5c.6 0 1 .4 1 1 0 1.3.2 2.5.6 3.6.1.3 0 .7-.2 1L6.6 10.8z"/></svg>
        913-555-0147
      </li>
      <li class="contact__item">
        <svg class="contact__icon" viewBox="0 0 24 24" aria-hidden="true"><circle cx="12" cy="12" r="10" fill="var(--ink)"/></svg>
        Rosalind Thorpe Gardens
      </li>
      <li class="contact__item">
        <svg class="contact__icon" viewBox="0 0 24 24" aria-hidden="true"><rect x="3" y="3" width="18" height="18" rx="3" fill="var(--ink)"/></svg>
        @RosalindThorpeGardens
      </li>
      <li class="contact__item">
        <svg class="contact__icon" viewBox="0 0 24 24" aria-hidden="true"><g fill="none" stroke="var(--ink)" stroke-width="2"><circle cx="12" cy="12" r="9"/><ellipse cx="12" cy="12" rx="4" ry="9"/><path d="M3 12h18"/></g></svg>
        www.RosalindThorpeGardens.example
      </li>
    </ul>
  </div>
</section>

<section class="card card--back" aria-label="Card back">
  <div class="brand-emboss">
    <span class="brand-emboss__name">Rosalind<br>Thorpe<br>Gardens</span>
  </div>
</section>

</body>
</html>
```